Independent Financial Advisor Billboard Campaign - Maple Crest Financial

I am a local, independent financial advisor. My company is Maple Crest Financial, located in Charleston, WV. My main source of revenue comes from those nearing or entering retirement that need assistance with financial planning and investment management. Many are looking to rollover their employer retirement plan into an IRA account. I would like a billboard design campaign that focuses on this type of client. Please see our website www.maplecrestfinancial.com for more information.

```html
<!DOCTYPE html>
<html lang="en">
<head>
<meta charset="utf-8">
<title>Maple Crest Financial – Billboard</title>
<link rel="stylesheet" href="https://fonts.googleapis.com/css2?family=Playfair+Display:wght@700;900&family=Poppins:wght@600;700&family=Cinzel:wght@600&display=swap">
<style>
  :root {
    --page-bg: #9a9a9a;
    --charcoal: #262626;
    --charcoal-soft: #3a3a3a;
    --navy: #1b4a86;
    --navy-deep: #143a6c;
    --steel: #5b5b5b;
    --white: #ffffff;
    --ink: #2b2b2b;
  }
  * { margin: 0; padding: 0; box-sizing: border-box; }
  html, body { width: 991px; height: 1200px; overflow: hidden; background: var(--page-bg); }
  .billboard {
    position: absolute; left: 30px; top: 464px;
    width: 931px; height: 272px;
    background: var(--white);
    box-shadow: 4px 8px 14px rgba(0,0,0,0.35);
    overflow: hidden;
  }
  .billboard__shapes { position: absolute; inset: 0; }
  .headline {
    position: absolute; left: 32px; top: 18px;
    font-family: "Playfair Display", Georgia, serif;
    font-weight: 900; font-size: 70px; line-height: 62px;
    color: var(--white); letter-spacing: 0.5px;
    text-transform: uppercase; white-space: nowrap;
  }
  .brand {
    position: absolute; left: 26px; top: 184px;
    display: flex; align-items: center; gap: 12px;
  }
  .brand__mark { width: 40px; height: 40px; background: var(--navy); }
  .brand__name {
    font-family: "Cinzel", Georgia, serif; font-weight: 600;
    font-size: 18px; line-height: 1.15; color: var(--navy);
  }
  .contact-phone {
    position: absolute; left: 298px; top: 168px;
    display: flex; align-items: center; gap: 6px;
    font-family: "Poppins", Arial, sans-serif; font-weight: 700;
    font-size: 38px; line-height: 40px; color: var(--ink);
    white-space: nowrap;
  }
  .contact-phone__icon { width: 32px; height: 32px; flex: none; }
  .contact-url {
    position: absolute; left: 293px; top: 216px;
    width: 372px; height: 28px; border-radius: 14px 0 0 14px;
    background: var(--navy);
    font-family: "Poppins", Arial, sans-serif; font-weight: 600;
    font-size: 15.5px; line-height: 28px; color: var(--white);
    padding-left: 16px; letter-spacing: 0.3px; white-space: nowrap;
  }
  .advisor-photo { position: absolute; left: 712px; top: 8px; width: 214px; height: 264px; }
</style>
</head>
<body>
  <section class="billboard">
    <svg class="billboard__shapes" width="931" height="272" viewBox="0 0 931 272" aria-hidden="true">
      <defs>
        <linearGradient id="darkBand" x1="0" y1="0" x2="1" y2="0">
          <stop offset="0" stop-color="#262626"/>
          <stop offset="0.6" stop-color="#262626"/>
          <stop offset="1" stop-color="#3a3a3a"/>
        </linearGradient>
      </defs>
      <rect x="0" y="0" width="931" height="157" fill="url(#darkBand)"/>
      <g fill="#ffffff" opacity="0.05">
        <rect x="560" y="110" width="12" height="47"/>
        <rect x="580" y="95" width="12" height="62"/>
        <rect x="600" y="100" width="12" height="57"/>
        <rect x="620" y="80" width="12" height="77"/>
        <rect x="640" y="70" width="12" height="87"/>
        <rect x="660" y="55" width="12" height="102"/>
      </g>
      <polyline points="540,40 590,30 630,48 680,22 720,12" fill="none" stroke="#ffffff" stroke-opacity="0.15" stroke-width="1"/>
      <polygon points="636,150 646,146 704,272 686,272" fill="#5b5b5b"/>
      <polygon points="719,0 931,0 931,272 704,272 646,146" fill="#1b4a86"/>
      <polygon points="760,40 931,40 931,272 760,272" fill="#143a6c" opacity="0.35"/>
    </svg>

    <h1 class="headline">Retirement<br>Done Right!</h1>

    <div class="brand">
      <span class="brand__mark"></span>
      <span class="brand__name">Maple Crest<br>Financial</span>
    </div>

    <div class="contact-phone">
      <svg class="contact-phone__icon" viewBox="0 0 34 34" aria-hidden="true">
        <circle cx="17" cy="17" r="17" fill="#1b4a86"/>
        <path d="M12 9c1-.6 2-.3 2.5.6l1.4 2.6c.4.8.2 1.6-.5 2.1l-1 .8c.8 1.9 2.2 3.4 4.1 4.3l.9-1c.6-.6 1.4-.7 2.1-.3l2.5 1.5c.8.5 1 1.5.5 2.4l-.7 1.2c-.6 1-1.8 1.5-3 1.2C15.2 23.9 10.6 19 9.6 13.4c-.2-1.2.3-2.4 1.3-3z" fill="#ffffff"/>
      </svg>
      <span>304.555.0142</span>
    </div>

    <div class="contact-url">www.maplecrestfinancial.com</div>

    <svg class="advisor-photo" viewBox="0 0 214 264" role="img" aria-label="Portrait photo of the advisor in a white polo shirt">
      <defs>
        <linearGradient id="photoTone" x1="0" y1="0" x2="0" y2="1">
          <stop offset="0" stop-color="#c9a98f" stop-opacity="0.5"/>
          <stop offset="0.45" stop-color="#e8e8ea"/>
          <stop offset="1" stop-color="#f4f4f6"/>
        </linearGradient>
      </defs>
      <rect x="0" y="0" width="214" height="264" fill="url(#photoTone)" opacity="0.9"/>
    </svg>
  </section>
</body>
</html>
```